New Business Card Design Project LORVANTI-Italy

we are LORVANTI-Italy
our company in the market for 3 years we are luxury cosmetic company and its about time for a facelift :)
i will like to have elegant luxurious and unique business card
that will give the person that get it a unique, luxurious and elegant impression
I'm VERY OPEN FOR NEW IDEAS , even duo i add a few files of things that i see on line and i like them

i add my logo as well
my website is LORVANTI.COM
(if you would like to see the main style that we have)

Target Market(s)

adult that have money :)

Industry/Entity Type

Business

Contact Information for Business Card

Name - Dario Lorvanti
Position - CEO and CO Founder
address - 4817 E Halvern
telephone - 555-384-1926
email - dario@lorvanti.com
fax - 555-384-1926
website - LORVANTI.COM

Colors
000000
959595
fbee3e
ffffff

Requirements
Must have
• big logo in GOLD color
• elegant look
• impressive
Nice to have
• not must but maybe classy pattern background
• not must but maybe emblem
• maybe clear plastic business card
Should not have
• colors
• images

```html
<!DOCTYPE html>
<html lang="en">
<head>
<meta charset="UTF-8">
<title>LORVANTI Italy – Business Card</title>
<link href="https://fonts.googleapis.com/css2?family=Cinzel:wght@500&family=Open+Sans:wght@400;600;700&display=swap" rel="stylesheet">
<style>
  :root {
    --backdrop: #2b2826;
    --card-black: #0c0c0c;
    --card-black-soft: #1a1a1a;
    --band-grey: #3a3a3a;
    --gold: #d8b54b;
    --gold-light: #f3d96a;
    --white: #ffffff;
    --ink: #111111;
  }
  * { margin: 0; padding: 0; box-sizing: border-box; }
  html, body { width: 1200px; height: 716px; overflow: hidden; }
  body {
    background: var(--backdrop);
    font-family: "Open Sans", Arial, sans-serif;
    position: relative;
  }
  .card {
    position: absolute;
    top: 208px;
    width: 525px;
    height: 300px;
    border-radius: 4px;
    overflow: hidden;
    background: linear-gradient(135deg, var(--card-black-soft), var(--card-black) 70%);
    box-shadow: 0 18px 40px rgba(0,0,0,.55);
  }
  .card--front { left: 55px; }
  .card--back { left: 620px; }

  .brand {
    position: absolute;
    left: 0; right: 0;
    display: flex;
    flex-direction: column;
    align-items: center;
  }
  .brand__disc {
    border: 3px solid var(--gold);
    border-radius: 50%;
  }
  .brand__name {
    font-family: "Cinzel", "Times New Roman", serif;
    font-weight: 500;
    color: var(--gold);
    letter-spacing: 1px;
  }
  .card--front .brand { top: 62px; }
  .card--front .brand__disc { width: 92px; height: 92px; margin-bottom: 14px; }
  .card--front .brand__name { font-size: 44px; }

  .card--back .brand { top: 22px; left: 40px; right: auto; width: 300px; }
  .card--back .brand__disc { width: 64px; height: 64px; margin-bottom: 8px; }
  .card--back .brand__name { font-size: 32px; }

  .card__art { position: absolute; inset: 0; }

  .holder {
    position: absolute;
    left: 32px;
    top: 146px;
    color: var(--white);
  }
  .holder__name { font-size: 14px; font-weight: 700; }
  .holder__role { font-size: 8px; opacity: .85; }

  .contact {
    position: absolute;
    display: flex;
    align-items: center;
    gap: 8px;
    color: var(--white);
    font-size: 12px;
    font-weight: 600;
  }
  .contact svg { width: 12px; height: 12px; flex: none; }
  .contact--phone { left: 30px; top: 196px; }
  .contact--email { left: 30px; top: 216px; }
  .contact--fax { left: 360px; top: 234px; }
  .contact--web { left: 360px; top: 254px; }
  .contact--address {
    left: 332px; top: 277px;
    color: var(--ink);
    font-size: 14px;
    font-weight: 700;
  }
</style>
</head>
<body>

  <section class="card card--front" aria-label="Card front">
    <div class="brand">
      <div class="brand__disc"></div>
      <div class="brand__name">LORVANTI</div>
    </div>
  </section>

  <section class="card card--back" aria-label="Card back">
    <svg class="card__art" viewBox="0 0 525 300" aria-hidden="true">
      <defs>
        <linearGradient id="goldStrip" x1="0" x2="1">
          <stop offset="0" stop-color="#c9a23c"/>
          <stop offset=".5" stop-color="#f3d96a"/>
          <stop offset="1" stop-color="#c9a23c"/>
        </linearGradient>
      </defs>
      <line x1="20" y1="180" x2="290" y2="180" stroke="var(--gold)" stroke-width="1.2"/>
      <rect x="0" y="186" width="525" height="114" fill="var(--band-grey)"/>
      <line x1="0" y1="186" x2="525" y2="186" stroke="var(--gold)" stroke-width="3"/>
      <line x1="0" y1="297" x2="525" y2="297" stroke="var(--gold)" stroke-width="3"/>
      <polygon points="300,272 525,272 525,300 288,300" fill="url(#goldStrip)"/>
    </svg>

    <div class="brand">
      <div class="brand__disc"></div>
      <div class="brand__name">LORVANTI</div>
    </div>

    <div class="holder">
      <div class="holder__name">Dario Lorvanti</div>
      <div class="holder__role">Position - CEO and CO Founder</div>
    </div>

    <div class="contact contact--phone">
      <svg viewBox="0 0 24 24"><path fill="var(--gold)" d="M6.6 10.8a15 15 0 0 0 6.6 6.6l2.2-2.2c.3-.3.7-.4 1-.2 1.1.4 2.3.6 3.6.6.6 0 1 .4 1 1V20c0 .6-.4 1-1 1A17 17 0 0 1 3 4c0-.6.4-1 1-1h3.5c.6 0 1 .4 1 1 0 1.3.2 2.5.6 3.6.1.3 0 .7-.2 1z"/></svg>
      <span>555-384-1926</span>
    </div>
    <div class="contact contact--email">
      <svg viewBox="0 0 24 24"><rect x="2" y="5" width="20" height="14" rx="1" fill="none" stroke="var(--gold)" stroke-width="2"/><path d="M2 6l10 7 10-7" fill="none" stroke="var(--gold)" stroke-width="2"/></svg>
      <span>dario@lorvanti.com</span>
    </div>
    <div class="contact contact--fax">
      <svg viewBox="0 0 24 24"><rect x="3" y="9" width="18" height="11" rx="1" fill="var(--gold)"/><rect x="7" y="3" width="10" height="7" fill="none" stroke="var(--gold)" stroke-width="2"/></svg>
      <span>555-384-1926</span>
    </div>
    <div class="contact contact--web">
      <svg viewBox="0 0 24 24"><circle cx="12" cy="12" r="9" fill="none" stroke="var(--gold)" stroke-width="2"/><path d="M3 12h18M12 3c3 3 3 15 0 18M12 3c-3 3-3 15 0 18" fill="none" stroke="var(--gold)" stroke-width="1.5"/></svg>
      <span>LORVANTI.COM</span>
    </div>
    <div class="contact contact--address">
      <svg viewBox="0 0 24 24"><path fill="var(--ink)" d="M12 2a7 7 0 0 0-7 7c0 5 7 13 7 13s7-8 7-13a7 7 0 0 0-7-7zm0 9.5A2.5 2.5 0 1 1 12 6.5a2.5 2.5 0 0 1 0 5z"/></svg>
      <span>4817 E Halvern</span>
    </div>
  </section>

</body>
</html>
```